Canadian Christian Church needs design for new sermon series

A graphic design for our series and an invitation card to invite people to the series. Check design brief for more detailed information. Target audience: young families and young adults. Looking for a creative design that will get people's attention and create interest. See design brief for copy of design purchased for previous series.
Updates
entered Apr 4 incorrectly. Need a week to receive and review designs, and today is Apr 2/19. Thanks!
Target Market(s)
young families and young adults
Colors
Designer to choose colors to be used in the design.
Look and feel

```html
<!DOCTYPE html>
<html lang="en">
<head>
<meta charset="utf-8">
<title>Messy – Sermon Series Invitation</title>
<link rel="stylesheet" href="https://fonts.googleapis.com/css2?family=Montserrat:wght@400;500;600;700&family=Oswald:wght@700&family=Roboto+Condensed:wght@400&family=Roboto+Slab:wght@400;600;700&display=swap">
<style>
  :root {
    --page-bg: #e4e4e4;
    --purple: #8a1f86;
    --blue: #1d5a8c;
    --orange: #e8891c;
    --ink: #2b2723;
    --beige: #cdc5af;
    --beige-light: #ddd6c3;
    --bar: #3b332d;
    --tick-blue: #2a6fb3;
    --white: #ffffff;
  }
  * { box-sizing: border-box; margin: 0; padding: 0; }
  html, body { width: 1200px; height: 903px; overflow: hidden; }
  body {
    position: relative;
    background: var(--page-bg);
    font-family: "Montserrat", sans-serif;
    color: var(--ink);
  }

  /* ---------- Front card ---------- */
  .card-front {
    position: absolute;
    left: 177px; top: 60px;
    width: 482px; height: 378px;
    overflow: hidden;
    box-shadow: 0 2px 5px rgba(0,0,0,.18);
  }
  .card-front .hero-photo {
    position: absolute; inset: 0;
    background:
      radial-gradient(ellipse at 48% 12%, #fffdf0 0%, #fbe9bf 22%, rgba(247,222,180,0) 55%),
      linear-gradient(180deg, #e9c9a6 0%, #f3dcc0 35%, #efe3cf 65%, #eae3d6 100%);
  }
  .card-front .inset-frame {
    position: absolute; inset: 8px;
    border: 1px solid rgba(255,255,255,.85);
  }
  .brand-front {
    position: absolute; left: 0; right: 0; top: 22px;
    display: flex; flex-direction: column; align-items: center; gap: 6px;
  }
  .brand-dot {
    width: 40px; height: 40px; border-radius: 50%;
    background: var(--orange);
    flex: none;
  }
  .brand-name {
    font-family: "Roboto Slab", serif;
    font-weight: 400;
    font-size: 13px;
    color: var(--ink);
    white-space: nowrap;
  }
  .series-title {
    position: absolute; right: 25px; top: 204px;
    font-family: "Oswald", sans-serif;
    font-weight: 700;
    font-size: 80px; line-height: 1;
    color: var(--purple);
    letter-spacing: 1px;
  }
  .series-subtitle {
    position: absolute; left: 23px; right: 23px; top: 292px;
    font-family: "Roboto Slab", serif;
    font-weight: 700;
    font-size: 32px; line-height: 1;
    color: var(--blue);
    letter-spacing: -0.6px;
    text-align: center;
    white-space: nowrap;
  }
  .front-rule {
    position: absolute; left: 23px; right: 23px; top: 333px;
    height: 1.5px; background: var(--orange);
  }
  .series-tagline {
    position: absolute; left: 23px; right: 23px; top: 340px;
    font-family: "Roboto Slab", serif;
    font-weight: 600;
    font-size: 19px; line-height: 1.1;
    color: var(--ink);
    text-align: center;
    white-space: nowrap;
  }

  /* ---------- Back card ---------- */
  .card-back {
    position: absolute;
    left: 582px; top: 470px;
    width: 484px; height: 378px;
    overflow: hidden;
    background:
      radial-gradient(ellipse 60% 35% at 80% 60%, rgba(255,255,255,.35), rgba(255,255,255,0) 70%),
      linear-gradient(160deg, var(--beige-light) 0%, var(--beige) 55%, #c6bea7 100%);
    box-shadow: 0 2px 5px rgba(0,0,0,.18);
  }
  .services-title {
    position: absolute; left: 0; right: 0; top: 23px;
    text-align: center;
    font-family: "Roboto Slab", serif;
    font-weight: 700;
    color: var(--ink);
    line-height: 1.12;
    white-space: nowrap;
  }
  .services-title .heading { font-size: 27px; display: block; letter-spacing: -0.3px; }
  .services-title .time { font-size: 27px; display: block; }

  .info-heading {
    position: absolute; left: 27px;
    font-weight: 700; font-size: 12px;
    color: var(--ink);
  }
  .info-list {
    position: absolute; left: 28px;
    list-style: none;
    font-size: 11px;
    line-height: 14.6px;
    color: var(--ink);
  }
  .info-list li { display: flex; align-items: center; gap: 6px; white-space: nowrap; }
  .info-list li strong { font-weight: 600; }
  .tick { width: 8px; height: 8px; flex: none; }

  .sermon-heading { top: 96px; }
  .sermon-list { top: 112px; }
  .features-heading { top: 240px; }
  .features-list { top: 256px; }

  .values-diagram {
    position: absolute; left: 294px; top: 95px;
    width: 170px; height: 162px;
    border-radius: 50%;
    background:
      conic-gradient(from 20deg, #1f6fb8 0 25%, #e8891c 25% 50%, #8b2c8e 50% 70%, #e8891c 70% 85%, #1f6fb8 85% 100%);
    -webkit-mask: radial-gradient(circle, transparent 30%, #000 31%);
            mask: radial-gradient(circle, transparent 30%, #000 31%);
  }

  .contact-bar {
    position: absolute; left: 0; top: 307px;
    width: 302px; height: 59px;
    background: var(--bar);
    color: var(--white);
    font-family: "Roboto Condensed", "Arial Narrow", sans-serif;
    font-size: 10px;
    padding: 6px 0 0 28px;
    line-height: 16px;
    overflow: hidden;
  }
  .contact-bar .row { display: flex; align-items: center; gap: 4px; white-space: nowrap; }
  .contact-bar .icon { width: 9px; height: 9px; flex: none; }
  .contact-bar .email { color: var(--orange); }
  .contact-bar .contact-person { margin-left: -5px; }

  .brand-back {
    position: absolute; left: 300px; top: 290px; width: 180px;
    display: flex; flex-direction: column; align-items: center; gap: 5px;
  }
  .brand-back .brand-dot { width: 44px; height: 44px; }
</style>
</head>
<body>

  <section class="card-front" aria-label="Sermon series card, front">
    <div class="hero-photo" role="img" aria-label="Photo of two hands reaching toward each other against a glowing golden sky"></div>
    <div class="inset-frame"></div>
    <div class="brand-front">
      <span class="brand-dot"></span>
      <span class="brand-name">Maple Grove Family Church</span>
    </div>
    <h1 class="series-title">MESSY</h1>
    <p class="series-subtitle">JOINING GOD IN THE MESS</p>
    <div class="front-rule"></div>
    <p class="series-tagline">CONNECTING YOUNG FAMILIES TO CHRIST</p>
  </section>

  <section class="card-back" aria-label="Sermon series card, back">
    <h2 class="services-title">
      <span class="heading">THE TIME OF THE SERVICES:</span>
      <span class="time">Sundays @ 10:30</span>
    </h2>

    <h3 class="info-heading sermon-heading">Names &amp; Dates of the sermons:</h3>
    <ul class="info-list sermon-list">
      <li><svg class="tick" viewBox="0 0 10 10"><circle cx="5" cy="5" r="5" fill="var(--tick-blue)"/><path d="M2.8 5.2l1.5 1.5 3-3.2" stroke="#fff" stroke-width="1.4" fill="none"/></svg><span><strong>April 28th:</strong> “We Made This Mess”</span></li>
      <li><svg class="tick" viewBox="0 0 10 10"><circle cx="5" cy="5" r="5" fill="var(--tick-blue)"/><path d="M2.8 5.2l1.5 1.5 3-3.2" stroke="#fff" stroke-width="1.4" fill="none"/></svg><span><strong>May 5th:</strong> “Bless in the Mess”</span></li>
      <li><svg class="tick" viewBox="0 0 10 10"><circle cx="5" cy="5" r="5" fill="var(--tick-blue)"/><path d="M2.8 5.2l1.5 1.5 3-3.2" stroke="#fff" stroke-width="1.4" fill="none"/></svg><span><strong>May 12th:</strong> “Born into the Mess”</span></li>
      <li><svg class="tick" viewBox="0 0 10 10"><circle cx="5" cy="5" r="5" fill="var(--tick-blue)"/><path d="M2.8 5.2l1.5 1.5 3-3.2" stroke="#fff" stroke-width="1.4" fill="none"/></svg><span><strong>May 19th:</strong> “Messy Work”</span></li>
      <li><svg class="tick" viewBox="0 0 10 10"><circle cx="5" cy="5" r="5" fill="var(--tick-blue)"/><path d="M2.8 5.2l1.5 1.5 3-3.2" stroke="#fff" stroke-width="1.4" fill="none"/></svg><span><strong>May 26th:</strong> “Messy Church”</span></li>
      <li><svg class="tick" viewBox="0 0 10 10"><circle cx="5" cy="5" r="5" fill="var(--tick-blue)"/><path d="M2.8 5.2l1.5 1.5 3-3.2" stroke="#fff" stroke-width="1.4" fill="none"/></svg><span><strong>June 2nd:</strong> “Messy Hospitality”</span></li>
      <li><svg class="tick" viewBox="0 0 10 10"><circle cx="5" cy="5" r="5" fill="var(--tick-blue)"/><path d="M2.8 5.2l1.5 1.5 3-3.2" stroke="#fff" stroke-width="1.4" fill="none"/></svg><span><strong>June 9th:</strong>&nbsp; TBD</span></li>
      <li><svg class="tick" viewBox="0 0 10 10"><circle cx="5" cy="5" r="5" fill="var(--tick-blue)"/><path d="M2.8 5.2l1.5 1.5 3-3.2" stroke="#fff" stroke-width="1.4" fill="none"/></svg><span><strong>June 16th:</strong> “Messy within Boundaries”</span></li>
    </ul>

    <h3 class="info-heading features-heading">Features of the service:</h3>
    <ul class="info-list features-list">
      <li><svg class="tick" viewBox="0 0 10 10"><circle cx="5" cy="5" r="5" fill="var(--tick-blue)"/><path d="M2.8 5.2l1.5 1.5 3-3.2" stroke="#fff" stroke-width="1.4" fill="none"/></svg><span>Staffed nursery &amp; children’s program every Sunday</span></li>
      <li><svg class="tick" viewBox="0 0 10 10"><circle cx="5" cy="5" r="5" fill="var(--tick-blue)"/><path d="M2.8 5.2l1.5 1.5 3-3.2" stroke="#fff" stroke-width="1.4" fill="none"/></svg><span>Coffee &amp; snacks</span></li>
      <li><svg class="tick" viewBox="0 0 10 10"><circle cx="5" cy="5" r="5" fill="var(--tick-blue)"/><path d="M2.8 5.2l1.5 1.5 3-3.2" stroke="#fff" stroke-width="1.4" fill="none"/></svg><span>Everyone welcome</span></li>
    </ul>

    <div class="values-diagram" role="img" aria-label="Illustrated ribbon diagram of the church's core values: equipping, serving, missional living, spirit-living and belonging"></div>

    <div class="contact-bar">
      <div class="row">
        <svg class="icon" viewBox="0 0 10 10"><path d="M5 9.5C3 7 2 5.5 2 4a3 3 0 0 1 6 0c0 1.5-1 3-3 5.5z" fill="none" stroke="var(--orange)" stroke-width="1.1"/><circle cx="5" cy="4" r="1" fill="var(--orange)"/></svg>
        <span>1875 Cedar Line West Oakridge, ON L4T 2R8</span>
      </div>
      <div class="row">
        <svg class="icon" viewBox="0 0 10 10"><path d="M2.2 1.2l1.6 1.8-.9 1.2c.6 1.2 1.5 2.1 2.7 2.7l1.2-.9 1.8 1.6-1 1.2C4.6 8.6 1.4 5.4 1 2.2z" fill="none" stroke="var(--orange)" stroke-width="1"/></svg>
        <span>905-555-0148</span>
        <svg class="icon" viewBox="0 0 10 10" style="margin-left:6px"><circle cx="5" cy="5" r="4" fill="none" stroke="var(--orange)" stroke-width="1"/><path d="M1 5h8M5 1c-2 2.5-2 5.5 0 8M5 1c2 2.5 2 5.5 0 8" fill="none" stroke="var(--orange)" stroke-width=".8"/></svg>
        <span>www.maplegrovechurch.ca</span>
      </div>
      <div class="row contact-person">
        <span>Please contact Laura Whitfield <span class="email">worship@maplegrovechurch.ca</span></span>
      </div>
    </div>

    <div class="brand-back">
      <span class="brand-dot"></span>
      <span class="brand-name">Maple Grove Family Church</span>
    </div>
  </section>

</body>
</html>
```